creation of a business card design for a company specializing in the creation...

I would like to create a design for a professional business card on a black background and with the company's colors (I am attaching some files: including the logo in horizontal and centered format, I am also attaching a recent project design a T-shirt, this is the one I chose to give you an idea of my preferences.

we are in the process of developing a new website design, it is still in the development phase but it can be viewed at the following address: www.vantrelmo.be to give you other ideas about the company
you will see for yourself the subject of my main activity: company specializing in the construction of stairs

I would like a business card that stands out from the rest with a unique design

here is the informations
Name: Lucien Barthel
Function: Manager
Address: Rue Moulinet du Parc 42
7180 La Louvière
telephone: +32 468 219 804
email: info@rx7p.be
website: rx7p. be
social networks: Facebook, YouTube, TikTok, Instagram

Target Market(s)

customer who wants to have a beautiful staircase built

Industry/Entity Type

contruction d'escalier

Contact Information for Business Card

Adresse. Numero de telephone, site web, le texte : "Createur d'escalier", logo recto-verso, icone des reseaux sociaux

Requirements
Must have
• the mention: Stair creator
Nice to have
• an illustration of a designer staircase
Should not have
• do not distort the logo

```html
<!DOCTYPE html>
<html lang="fr">
<head>
<meta charset="utf-8">
<title>RX7P – Carte de visite</title>
<link rel="stylesheet" href="https://fonts.googleapis.com/css2?family=Open+Sans:wght@400;600&display=swap">
<style>
  :root {
    --stage: #232323;
    --card: #1d1e21;
    --card-deep: #141517;
    --accent: #6b9aba;
    --accent-soft: #8fb6d0;
    --text: #f1f1f1;
    --muted: #9aa3aa;
  }
  * { box-sizing: border-box; margin: 0; padding: 0; }
  html, body { width: 1200px; height: 780px; overflow: hidden; }
  body {
    background: var(--stage);
    font-family: "Open Sans", Arial, sans-serif;
    color: var(--text);
    display: flex;
    align-items: center;
    justify-content: center;
    gap: 40px;
  }
  .card {
    position: relative;
    width: 540px;
    height: 310px;
    background: var(--card);
    border-radius: 4px;
    box-shadow: 0 18px 40px rgba(0,0,0,.55);
    overflow: hidden;
  }

  /* Front: contact side */
  .brand {
    position: absolute;
    top: 24px;
    left: 30px;
    display: flex;
    align-items: center;
    gap: 10px;
  }
  .brand-dot {
    width: 34px; height: 34px;
    border-radius: 50%;
    background: var(--accent);
    flex: none;
  }
  .brand-name {
    font-size: 24px;
    font-weight: 600;
    letter-spacing: 3px;
    color: var(--text);
    line-height: 1;
  }
  .mention {
    position: absolute;
    top: 66px;
    left: 30px;
    font-size: 11px;
    font-weight: 600;
    letter-spacing: 2px;
    text-transform: uppercase;
    color: var(--accent-soft);
  }
  .address {
    position: absolute;
    top: 98px;
    left: 30px;
    font-size: 13px;
    line-height: 1.45;
  }
  .contacts {
    position: absolute;
    top: 152px;
    left: 30px;
    list-style: none;
    font-size: 13px;
    line-height: 1.6;
  }
  .contacts li { display: flex; align-items: center; gap: 8px; }
  .contacts svg { width: 12px; height: 12px; fill: var(--accent); flex: none; }
  .holder {
    position: absolute;
    right: 40px;
    bottom: 40px;
    text-align: right;
  }
  .holder-name {
    font-size: 28px;
    font-weight: 600;
    color: var(--accent-soft);
    line-height: 1.15;
  }
  .holder-role { font-size: 15px; color: var(--text); }
  .edge-bar {
    position: absolute;
    right: 0;
    bottom: 36px;
    width: 16px;
    height: 66px;
    background: var(--accent);
  }

  /* Back: brand side */
  .card-back { background: var(--card-deep); }
  .pattern {
    position: absolute;
    inset: 0;
    background: linear-gradient(120deg, #121315 0%, #1a1b1e 55%, #4a4d52 100%);
  }
  .back-brand {
    position: absolute;
    inset: 0;
    display: flex;
    align-items: center;
    justify-content: center;
    gap: 16px;
  }
  .back-square {
    width: 54px; height: 54px;
    background: var(--accent);
  }
  .back-name {
    font-size: 56px;
    font-weight: 600;
    letter-spacing: 6px;
    color: var(--text);
  }
</style>
</head>
<body>

<section class="card card-front">
  <div class="brand">
    <span class="brand-dot"></span>
    <span class="brand-name">RX7P</span>
  </div>
  <p class="mention">Créateur d'escalier</p>

  <p class="address">Rue Moulinet du Parc 42<br>7180 La Louvière</p>

  <ul class="contacts">
    <li>
      <svg viewBox="0 0 24 24"><path d="M6.6 10.8a15.1 15.1 0 0 0 6.6 6.6l2.2-2.2c.3-.3.7-.4 1-.2 1.1.4 2.3.6 3.6.6.6 0 1 .4 1 1V20c0 .6-.4 1-1 1A17 17 0 0 1 3 4c0-.6.4-1 1-1h3.5c.6 0 1 .4 1 1 0 1.3.2 2.5.6 3.6.1.3 0 .7-.2 1z"/></svg>
      +32 468 219 804
    </li>
    <li>
      <svg viewBox="0 0 24 24"><path d="M2 5h20v14H2zm2 2v.5l8 5 8-5V7zm0 2.8V17h16V9.8l-8 5z"/></svg>
      info@rx7p.be
    </li>
    <li>
      <svg viewBox="0 0 24 24"><path d="M12 2a10 10 0 1 0 0 20 10 10 0 0 0 0-20zm0 2a8 8 0 0 1 7.7 6H4.3A8 8 0 0 1 12 4zm-7.7 8h15.4a8 8 0 0 1-15.4 0z"/></svg>
      www.rx7p. be
    </li>
  </ul>

  <div class="holder">
    <p class="holder-name">Lucien Barthel</p>
    <p class="holder-role">Manager</p>
  </div>
  <span class="edge-bar"></span>
</section>

<section class="card card-back">
  <div class="pattern" role="img" aria-label="Repeating pattern of small brand marks fading from black to silver"></div>
  <div class="back-brand">
    <span class="back-square"></span>
    <span class="back-name">RX7P</span>
  </div>
</section>

</body>
</html>
```